we can communicate on this, but i want to follow the approach we took on Pellew|Marsh & Quinlan but i feel the card front needs the black background and the platinum and gold logo. The back? I am open. we can use the same info from PM&Q. Velmont Arc is an enhanced equity investment fund - basically a very exclusive boutique hedge fund that uses only stock options. very advanced things. hope you are interested

Contact Information for Business Card

Dr. Lewis T. Brennick, CFA
Scientifique de fusée financière
701.555.0143
LTBquant47@mailvantor.com

4718 Willow Creek Bend W.
West Fargo, ND 58078

No web site

Colors

Designer to choose colors to be used in the design.

Requirements
Nice to have
• I tend to prefer the most visible applications of the logo to include logo and name, the logo version with a black background and the gold and platinum components separated by the black. I see this working well for a single side (logo and name - this is card front to me).
• I am fairly open to other treatments on the reverse side with the data. To me, it makes sense to have a different color rendition of the logo on the reverse and it may be a muted black tone on tone or an oversized portion that would have spot UV. Or, the reverse may play with colors and layout
Should not have
• Other colors = no no
• Decorative font

```html
<!DOCTYPE html>
<html lang="en">
<head>
<meta charset="utf-8">
<title>Velmont Arc — Business Card</title>
<link href="https://fonts.googleapis.com/css2?family=Montserrat:wght@400;500;600&display=swap" rel="stylesheet">
<style>
  :root {
    --stage: #2a2a2a;
    --card-black: #1b1b1b;
    --card-white: #ffffff;
    --card-white-shade: #e6e6e6;
    --gold: #c9a233;
    --gold-light: #e0bf62;
    --platinum: #c9c9c9;
    --ink: #1a1a1a;
  }
  * { margin: 0; padding: 0; box-sizing: border-box; }
  html, body { width: 1200px; height: 900px; overflow: hidden; }
  body {
    background: var(--stage);
    font-family: "Montserrat", sans-serif;
    display: flex;
    align-items: center;
    justify-content: center;
    gap: 40px;
  }
  .card {
    width: 540px;
    height: 309px;
    border-radius: 16px;
    position: relative;
    overflow: hidden;
  }
  .card-front {
    background: var(--card-black);
    display: flex;
    align-items: center;
    justify-content: center;
    gap: 22px;
  }
  .brand-dot {
    width: 62px;
    height: 62px;
    border-radius: 50%;
    background: var(--gold);
  }
  .brand-name {
    font-weight: 600;
    font-size: 40px;
    letter-spacing: 2px;
    text-transform: uppercase;
    color: var(--platinum);
  }
  .card-back {
    background: linear-gradient(135deg, var(--card-white) 40%, var(--card-white-shade));
  }
  .back-feature {
    position: absolute;
    right: -120px;
    bottom: -190px;
    width: 420px;
    height: 420px;
  }
  .contact {
    position: absolute;
    left: 30px;
    top: 30px;
    color: var(--ink);
    font-size: 13px;
    line-height: 1.5;
  }
  .person-name {
    color: var(--gold);
    font-weight: 500;
    font-size: 18px;
    text-transform: uppercase;
    letter-spacing: 0.5px;
  }
  .person-title { font-size: 13px; margin-bottom: 14px; }
  .address { margin-bottom: 14px; }
  .contact-line { display: flex; align-items: center; gap: 8px; }
  .contact-line svg { width: 12px; height: 12px; flex: none; }
</style>
</head>
<body>
  <section class="card card-front">
    <span class="brand-dot"></span>
    <span class="brand-name">Velmont Arc</span>
  </section>

  <section class="card card-back">
    <svg class="back-feature" viewBox="0 0 420 420" role="img" aria-label="Oversized gold and platinum brand decoration">
      <defs>
        <linearGradient id="feature-tone" x1="0" y1="0" x2="1" y2="1">
          <stop offset="0" stop-color="#e0bf62"/>
          <stop offset="0.6" stop-color="#c9a233"/>
          <stop offset="1" stop-color="#9a9a9a"/>
        </linearGradient>
      </defs>
      <circle cx="210" cy="210" r="210" fill="url(#feature-tone)"/>
    </svg>

    <div class="contact">
      <p class="person-name">Dr. Lewis T. Brennick, CFA</p>
      <p class="person-title">Scientifique de fusée financière</p>
      <p class="address">4718 Willow Creek Bend W.<br>West Fargo, ND 58078</p>
      <p class="contact-line">
        <svg viewBox="0 0 24 24" aria-hidden="true"><path fill="#c9a233" d="M6.6 10.8a15 15 0 0 0 6.6 6.6l2.2-2.2a1 1 0 0 1 1-.25 11.4 11.4 0 0 0 3.6.57 1 1 0 0 1 1 1V20a1 1 0 0 1-1 1A17 17 0 0 1 3 4a1 1 0 0 1 1-1h3.5a1 1 0 0 1 1 1c0 1.25.2 2.45.57 3.6a1 1 0 0 1-.25 1z"/></svg>
        701.555.0143
      </p>
      <p class="contact-line">
        <svg viewBox="0 0 24 24" aria-hidden="true"><rect x="3" y="5" width="18" height="14" rx="2" fill="none" stroke="#c9a233" stroke-width="2"/><path d="M3 7l9 6 9-6" fill="none" stroke="#c9a233" stroke-width="2"/></svg>
        LTBquant47@mailvantor.com
      </p>
    </div>
  </section>
</body>
</html>
```